Permanent Makeup (cosmetics salon) Brochure

We need a 2-4 sites brochure for our Permanent Makeup (cosmetics salon). Our company is based in Austria / Vienna. -> Our homepage is www.ek-morgenstaller.at
This brochure should show which treatments we provide ot our customers.

I've uploaded our old brochure, the content (text) would be nearly the same (look form "Must Haves", pics have to be new (look uploaded pics)
The old brochure is to dark. -> look for our homepage maybe you can make it like this

Target Market(s)

woman, age 25-70 years who wants to have permanent makeup on eyebrows, lips or eyeliner

Industry/Entity Type

Beauty Salon

Requirements
Must have
• pics which are uploaded.

*This text (somithing about our business)
"Für Frau Morgenstaller ist Permanent Makeup ein Kunsthandwerk. Das Team von EK-Morgenstaller ist spezialisiert auf natürliches Permanent Makeup damit der individuelle Typ jeder Kundin am schönsten zum Ausdruck kommt."

*We do this treatments: (english)
+ Augenbrauen Microblading (eyebrows)
+ Augenbrauen Permanent Makeup (eyebrows2)
+ Lidstrich Permanent Makeup (eyeliner)
+ Lip Blushing (lips)
+ Lippen Permanent Makeup (lips2)

* Our addresses (2 locations)
Wien
Lindengasse 7b/12, 1010 Wien
Tel: 01/5827710

Villach
Birkenrainweg 4, 9524 St. Ulrich
Tel: 0676/3159082

Mail: info@ek-morgenstaller.at
www.ek-morgenstaller.at

```html
<!DOCTYPE html>
<html lang="de">
<head>
<meta charset="utf-8">
<title>EK-Morgenstaller Brochure</title>
<link rel="stylesheet" href="https://fonts.googleapis.com/css2?family=Source+Sans+3:wght@300;400;600;700&family=Source+Serif+4:wght@400;600&display=swap">
<style>
:root{
  --stage:#cccccc;
  --yellow:#e8c462;
  --dark:#403e3c;
  --paper:#f5f4f1;
  --grey:#9a9896;
  --white:#ffffff;
  --sans:"Source Sans 3", Arial, sans-serif;
  --serif:"Source Serif 4", Georgia, serif;
}
*{margin:0;padding:0;box-sizing:border-box}
html,body{width:1044px;height:1200px;overflow:hidden;background:var(--stage)}
.canvas{position:relative;width:1044px;height:1200px;font-family:var(--sans);color:var(--dark)}
.abs{position:absolute}
.c{position:absolute;transform:translate(-50%,-50%);white-space:nowrap;line-height:1}
.page{position:absolute;overflow:hidden}
.bar{position:absolute;height:2.5px;background:var(--dark)}
.bar i{position:absolute;left:0;top:0;height:100%;background:var(--yellow)}
.photo{position:absolute}
.brand-name{position:absolute;transform:translate(-50%,-50%);white-space:nowrap;color:var(--white);font-family:var(--sans);font-weight:400;font-size:9px;letter-spacing:.6px;line-height:1}

/* cover */
.cover{left:133px;top:106px;width:329px;height:422px;background:var(--paper)}
.cover .photo{left:0;top:0;width:202px;height:422px;background:linear-gradient(160deg,#b59684 0%,#d3b09b 35%,#c49c86 60%,#6d6a6c 100%)}
.cover .accent-y{left:186px;top:0;width:3px;height:117px;background:var(--yellow)}
.cover .accent-d{left:186px;top:117px;width:3px;height:368px;background:#4a4f57}
.cover .logo-band{left:0;top:381px;width:202px;height:41px;background:rgba(64,62,60,.75)}
.headline .beauty{font-family:var(--serif);font-weight:600;color:var(--yellow);font-size:29px;left:41px;top:283px;position:absolute;line-height:1}
.headline .sub{font-family:var(--serif);color:var(--white);font-size:15.5px;left:41px;top:310px;position:absolute;line-height:1}
.headline .big{font-family:var(--serif);color:var(--white);font-size:23px;left:41px;top:330px;position:absolute;line-height:1}
.cover .intro{right:29px;top:31px;width:80px;text-align:right;font-size:5.8px;line-height:7.5px;color:var(--dark)}
.cover .claim{left:189px;top:158px;width:140px;height:158px;background:var(--yellow)}
.claim .l1{font-weight:700;color:var(--white);font-size:16px;left:70px;top:63px}
.claim .l2{font-size:14px;left:70px;top:80px;color:var(--dark)}
.claim .l3{font-weight:300;font-size:13px;left:70px;top:97px;color:var(--dark)}
.cover .web-band{left:202px;top:381px;width:127px;height:41px;background:var(--grey)}
.web-band .c{left:63px;top:19px;font-size:6.5px;font-weight:700;letter-spacing:1px;color:var(--dark)}

/* contact page */
.contact{left:595px;top:106px;width:329px;height:424px;background:var(--yellow)}
.contact .eyes{left:0;top:0;width:329px;height:162px;background:linear-gradient(180deg,#b89a88 0%,#d9bcaa 45%,#cfae9a 100%)}
.contact .info-band{left:0;top:162px;width:329px;height:50px}
.info-row{position:absolute;display:flex;align-items:center;gap:6px;font-size:7.5px;font-weight:600;color:var(--dark)}
.contact .brand-band{left:0;top:212px;width:329px;height:38px;background:var(--dark)}
.branches .title{font-size:9px;font-weight:600;color:var(--white);left:165px;top:282px}
.branch .name{font-size:6px;top:307px}
.branch .line{font-size:6px;font-weight:700}
.contact .lips{left:0;top:343px;width:130px;height:81px;background:linear-gradient(180deg,#e3c2b2 0%,#cf9c8e 55%,#e6c9ba 100%)}
.contact .divider{left:130px;top:372px;width:3px;height:46px;background:var(--dark)}
.contact .blonde{left:133px;top:343px;width:196px;height:81px;background:linear-gradient(100deg,#e9dccd 0%,#d9bca4 50%,#c79a7e 100%)}

/* services spread */
.spread{left:205px;top:661px;width:648px;height:423px;background:var(--paper)}
.spread .yellow-half{left:325px;top:0;width:323px;height:423px;background:var(--yellow)}
.spread .mouth{left:0;top:34px;width:446px;height:355px;background:linear-gradient(180deg,#caa28f 0%,#d6ae9c 30%,#cf8d86 55%,#c58a80 70%,#b78e7d 100%)}
.spread .text-band{left:0;top:292px;width:446px;height:97px;background:rgba(110,96,88,.72)}
.text-band p{position:absolute;left:50%;top:26px;transform:translateX(-50%);width:215px;text-align:center;color:var(--white);font-size:7px;font-weight:400;line-height:10px;letter-spacing:.6px}
.services-head{position:absolute;left:517px;top:72px;line-height:1}
.services-head .t{font-size:12.5px;font-weight:600;color:var(--dark)}
.services-head .t b{color:var(--white);font-weight:700}
.services-head .s{font-size:9.3px;margin-top:3px}
.service .name{font-weight:700;color:var(--white);font-size:8px;letter-spacing:.3px}
.service .item{font-size:9.3px}
</style>
</head>
<body>
<div class="canvas">

  <!-- Cover page -->
  <section class="page cover">
    <div class="photo" role="img" aria-label="Close-up portrait photo of a woman with natural makeup"></div>
    <div class="abs accent-y"></div>
    <div class="abs accent-d"></div>
    <div class="abs logo-band"></div>
    <div class="headline">
      <span class="beauty">BEAUTY</span>
      <span class="sub">not only comes</span>
      <span class="big">from Inside</span>
    </div>
    <span class="brand-name" style="left:101px;top:401px">Elka Morgenstaller</span>
    <p class="abs intro">Für Frau Morgenstaller ist Permanent Makeup ein Kunsthandwerk. Das Team von EK-Morgenstaller ist spezialisiert auf natürliches Permanent Makeup damit der individuelle Typ jeder Kundin am schönsten zum Ausdruck kommt.</p>
    <div class="abs claim">
      <span class="c l1">Schönheit</span>
      <span class="c l2">kommt nicht</span>
      <span class="c l3">nur von innen</span>
    </div>
    <div class="bar" style="left:202px;top:378px;width:122px"><i style="width:45px"></i></div>
    <div class="abs web-band"><span class="c">WWW.EK-MORGENSTALLER.AT</span></div>
  </section>

  <!-- Contact page -->
  <section class="page contact">
    <div class="photo eyes" role="img" aria-label="Close-up photo of a woman's eyes and eyebrows"></div>
    <div class="bar" style="left:14px;top:40px;width:252px"><i style="width:95px"></i></div>
    <div class="abs info-band">
      <div class="info-row" style="top:12px;left:104px">
        <svg width="12" height="12" viewBox="0 0 12 12" fill="none" stroke="#403e3c" stroke-width=".9"><circle cx="6" cy="6" r="5"/><ellipse cx="6" cy="6" rx="2.2" ry="5"/><path d="M1 6h10M1.8 3.5h8.4M1.8 8.5h8.4"/></svg>
        <span>WWW.EK-MORGENSTALLER.AT</span>
      </div>
      <div class="info-row" style="top:27px;left:106px">
        <svg width="12" height="12" viewBox="0 0 12 12" fill="none" stroke="#403e3c" stroke-width=".9"><circle cx="6" cy="6" r="5"/><path d="M4.5 4.6a1.6 1.6 0 1 1 2.2 1.4c-.5.2-.7.6-.7 1.1"/><circle cx="6" cy="8.8" r=".4" fill="#403e3c"/></svg>
        <span>INFO@EK-MORGENSTALLER.AT</span>
      </div>
    </div>
    <div class="abs brand-band"></div>
    <span class="brand-name" style="left:165px;top:231px;font-size:8px">Elka Morgenstaller</span>
    <svg class="abs" style="left:157px;top:260px" width="16" height="14" viewBox="0 0 16 14" fill="none" stroke="#403e3c" stroke-width="1"><path d="M2 1h12l1.5 4h-15z"/><path d="M2 5v8h12V5"/><rect x="4" y="8" width="3" height="5"/><rect x="9" y="7.5" width="3" height="2.5"/></svg>
    <div class="branches">
      <span class="c title">OUR BRANCHES</span>
      <div class="branch">
        <span class="c name" style="left:106px">VILLACH BRANCH</span>
        <span class="c line" style="left:106px;top:322px">BIRKENRAINWEG 4, 9524 ST. ULRICH</span>
        <span class="c line" style="left:106px;top:330px">TEL: 0676/3159082</span>
      </div>
      <div class="branch">
        <span class="c name" style="left:235px">WIEN BRANCH</span>
        <span class="c line" style="left:235px;top:322px">LINDENGASSE 7b/12, 1010 WIEN</span>
        <span class="c line" style="left:235px;top:330px">TEL: 01/5827710</span>
      </div>
    </div>
    <div class="photo lips" role="img" aria-label="Close-up photo of natural lips"></div>
    <div class="abs divider"></div>
    <div class="photo blonde" role="img" aria-label="Photo of a blonde woman's eye area"></div>
    <div class="bar" style="left:146px;top:357px;width:156px"><i style="width:59px"></i></div>
  </section>

  <!-- Services spread -->
  <section class="page spread">
    <div class="abs yellow-half"></div>
    <div class="photo mouth" role="img" aria-label="Close-up photo of lips with permanent lip blushing"></div>
    <div class="bar" style="left:12px;top:112px;width:102px"><i style="width:38px"></i></div>
    <div class="abs text-band">
      <p>Für Frau Morgenstaller ist Permanent Makeup ein Kunsthandwerk. Das Team von EK-Morgenstaller ist spezialisiert auf natürliches Permanent Makeup damit der individuelle Typ jeder Kundin am schönsten zum Ausdruck kommt.</p>
    </div>
    <div class="bar" style="left:172px;top:378px;width:329px"><i style="width:123px"></i></div>

    <svg class="abs" style="left:486px;top:68px" width="22" height="22" viewBox="0 0 22 22" fill="none" stroke="#403e3c" stroke-width=".9"><circle cx="8" cy="7" r="4"/><path d="M2 21c0-5 3-8 6-8s6 3 6 8"/><rect x="14" y="1" width="7" height="5" rx="1"/><path d="M15.5 3h4M15.5 4.5h3"/><path d="M15 13l4-3"/></svg>
    <div class="services-head">
      <div class="t"><b>OUR</b> SERVICES</div>
      <div class="s">We do this treatments</div>
    </div>

    <div class="service">
      <svg class="abs" style="left:532px;top:136px" width="26" height="18" viewBox="0 0 26 18" fill="none" stroke="#403e3c" stroke-width="1.6" stroke-linecap="round"><path d="M2 6c6-6 15-6 22 1" stroke-width="2.6"/><path d="M5 10c5 4 11 4 16 0"/><path d="M8 13l-1 3M13 14v3M18 13l1 3"/></svg>
      <span class="c name" style="left:545px;top:168px">EYEBROWS</span>
      <span class="c item" style="left:545px;top:183px">Augenbrauen Microblading</span>
      <span class="c item" style="left:545px;top:199px">Augenbrauen Permanent Makeup</span>
    </div>

    <div class="service">
      <svg class="abs" style="left:531px;top:226px" width="28" height="20" viewBox="0 0 28 20" fill="none" stroke="#403e3c" stroke-width="1.6"><path d="M3 3c7-4 15-3 22 4" stroke-width="2"/><path d="M2 12c7-8 17-8 24 0c-7 7-17 7-24 0z"/><circle cx="14" cy="11.5" r="3.5" fill="#403e3c"/></svg>
      <span class="c name" style="left:545px;top:258px">EYELINER</span>
      <span class="c item" style="left:545px;top:272px">Lidstrich Permanent Makeup</span>
    </div>

    <div class="service">
      <svg class="abs" style="left:532px;top:296px" width="26" height="14" viewBox="0 0 26 14"><path d="M1 6c4-2 7-5 9-5c1.5 0 2.300 1 3 1s1.5-1 3-1c2 0 5 3 9 5c-4 4-8 7-12 7s-8-3-12-7z" fill="#403e3c"/><path d="M2 6.5c7 1.5 15 1.5 22 0" stroke="#e8c462" stroke-width="1" fill="none"/></svg>
      <span class="c name" style="left:545px;top:321px">LIPS</span>
      <span class="c item" style="left:545px;top:335px">Lip Blushing</span>
      <span class="c item" style="left:545px;top:350px">Lippen Permanent Makeup</span>
    </div>
  </section>

</div>
</body>
</html>
```